New business card for a regional office of a US M&A company

We need business card for a finance company, office based in Hong Kong , our Head office is in US, our business is to Merge and acquires companies , the new office will be a regional office for the Asia Pacific region. We want to use the head office logo as attached ( but don't have to be exactly the same, can be a variation to it) as a base and then add Asia Pacific alongside the logo.
We would prefer to have be bilingual Eng + Chinese, although we don't really have Chinese company name .

Industry/Entity Type

Business

Contact Information for Business Card

Clara Jo Tsang
 

VP,
APAC M&A Operations
Orin Vantage Asia Pacific Limited
 
Unit 1407, K18
18 Tai Lok Shan Road, 
Hong Kong 
 
M: +852 6038 1742
T : +852 2836 4100
F : +852 2836 4177
VOIP: 4158
 
cjtsang@orinvantage.com

Font styles to use
Serif
Sans Serif

Colors

Designer to choose colors to be used in the design.

Requirements
Must have
• APAC Office

```html
<!DOCTYPE html>
<html lang="en">
<head>
<meta charset="utf-8">
<title>Orin Vantage Asia Pacific – Business Card</title>
<link href="https://fonts.googleapis.com/css2?family=Open+Sans:wght@400;600;700;800&display=swap" rel="stylesheet">
<style>
  :root {
    --backdrop: #3a3a3c;
    --card: #1e1f22;
    --ink-dim: #4a4b50;
    --accent: #1aa9cf;
    --white: #f2f4f5;
    --soft: #d9dcde;
  }
  * { margin: 0; padding: 0; box-sizing: border-box; }
  html, body { width: 799px; height: 1200px; overflow: hidden; }
  body {
    background: var(--backdrop);
    font-family: "Open Sans", sans-serif;
    position: relative;
  }
  .card {
    position: absolute;
    left: 70px;
    width: 660px;
    height: 380px;
    background: var(--card);
    box-shadow: 0 10px 30px rgba(0,0,0,.45);
    overflow: hidden;
  }
  .card--front { top: 150px; }
  .card--back { top: 680px; }

  /* Front */
  .front-brand {
    position: absolute;
    left: 0; right: 0; top: 150px;
    display: flex; align-items: center; justify-content: center; gap: 18px;
  }
  .front-brand__square {
    width: 44px; height: 44px;
    border: 7px solid var(--ink-dim);
  }
  .front-brand__name {
    font-weight: 800;
    font-size: 50px;
    letter-spacing: 1px;
    color: var(--ink-dim);
  }

  /* Back */
  .back-brand {
    position: absolute;
    left: 36px; top: 130px;
    width: 230px;
    display: flex; flex-direction: column; align-items: center; gap: 14px;
  }
  .back-brand__square {
    width: 60px; height: 60px;
    background: var(--white);
  }
  .back-brand__name {
    font-weight: 800;
    font-size: 26px;
    color: var(--white);
    letter-spacing: .5px;
  }
  .divider {
    position: absolute;
    left: 290px; top: 40px;
    width: 1px; height: 250px;
    background: var(--accent);
  }
  .details {
    position: absolute;
    left: 318px; top: 38px;
    right: 20px;
    color: var(--soft);
  }
  .details__name {
    font-weight: 700; font-size: 22px; color: var(--accent);
    line-height: 1.2;
  }
  .details__title {
    font-size: 15px; line-height: 1.3; color: var(--white);
    margin-top: 4px;
  }
  .details__company {
    font-weight: 700; font-size: 16px; color: var(--accent);
    margin-top: 14px;
  }
  .contacts { list-style: none; margin-top: 10px; }
  .contacts li {
    display: flex; align-items: center; gap: 10px;
    font-size: 15px; line-height: 1.45; color: var(--white);
  }
  .contacts svg { width: 14px; height: 14px; flex: none; }
  .contacts .label { color: var(--accent); margin-left: 6px; }

  .address-band {
    position: absolute;
    left: 0; right: 0; bottom: 0;
    height: 50px;
    background: var(--accent);
    color: var(--white);
    font-size: 17px;
    display: flex; align-items: center;
    padding-left: 30px;
  }
</style>
</head>
<body>

<section class="card card--front">
  <div class="front-brand">
    <div class="front-brand__square"></div>
    <div class="front-brand__name">ORIN VANTAGE</div>
  </div>
</section>

<section class="card card--back">
  <div class="back-brand">
    <div class="back-brand__square"></div>
    <div class="back-brand__name">ORIN VANTAGE</div>
  </div>

  <div class="divider"></div>

  <div class="details">
    <div class="details__name">Clara Jo Tsang</div>
    <div class="details__title">Vice President,<br>APAC M&amp;A Operations</div>
    <div class="details__company">Orin Vantage Asia Pacific Limited</div>
    <ul class="contacts">
      <li>
        <svg viewBox="0 0 14 14" aria-hidden="true"><rect x="3.5" y="1" width="7" height="12" rx="1.2" fill="none" stroke="#1aa9cf" stroke-width="1.6"/><circle cx="7" cy="10.8" r=".9" fill="#1aa9cf"/></svg>
        +852 6038 1742
      </li>
      <li>
        <svg viewBox="0 0 14 14" aria-hidden="true"><path d="M2 5c0-2 2-3 5-3s5 1 5 3v1H9.5V4.5h-5V6H2z" fill="#1aa9cf"/><rect x="3" y="7" width="8" height="5" rx="1" fill="#1aa9cf"/></svg>
        +852 2836 4100
      </li>
      <li>
        <svg viewBox="0 0 14 14" aria-hidden="true"><rect x="4" y="1" width="6" height="4" fill="none" stroke="#1aa9cf" stroke-width="1.4"/><rect x="1.5" y="5" width="11" height="6" rx="1" fill="#1aa9cf"/><rect x="4" y="9" width="6" height="4" fill="#1aa9cf"/></svg>
        <span>+852 2836 4177,<span class="label">VOIP:</span> 4158</span>
      </li>
      <li>
        <svg viewBox="0 0 14 14" aria-hidden="true"><rect x="1" y="3" width="12" height="8" rx="1" fill="#1aa9cf"/><path d="M1.5 3.5 7 8l5.5-4.5" fill="none" stroke="#1e1f22" stroke-width="1.2"/></svg>
        cjtsang@orinvantage.com
      </li>
    </ul>
  </div>

  <div class="address-band">Unit 1407, K18 18, Tai Lok Shan Road, Hong Kong</div>
</section>

</body>
</html>
```